Refresh of far from plain IT company website

Our web site is starting to show it's age. You can see the existing site here: www.plumbwick.net. As a growing company we want to come across as a dynamic collection of IT experts.

We want to update the design so are open to any colour palette and look, but want to retain our current table logo. We use the logo on our business cards but with a white background - see the attached file, so you don't need to keep the brown or the green.

The design should consider the range of browsers that will be looking at the site - so please show how it will look on a wide screen laptop and a 768x1024 tablet.

We want to add some pages about our team and their skills, probably with photos of each person on the team.

This is an uncoded project - the PSD files of the design is required, not coding.
Updates

Thanks everyone for the submissions so far.  It's a holiday day in the UK today but we will get some feedback on the designs so far out to you.

Target Market(s)

Architects and other creative types looking for IT support

Industry/Entity Type

Business

Font styles to use
Serif
Sans Serif

Requirements
Must have
• Must look good on a laptop and an iPad.

```html
<!DOCTYPE html>
<html lang="en">
<head>
<meta charset="utf-8">
<title>plumbwick – IT support and management</title>
<link href="https://fonts.googleapis.com/css2?family=Open+Sans:ital,wght@0,300;0,400;0,600;1,400&display=swap" rel="stylesheet">
<style>
:root{
  --plum:#8b1452;
  --gold:#c8901a;
  --ink:#333;
  --muted:#555;
  --grey-circle:#efefef;
  --yellow:#fdf0c0;
  --footer:#dcdcdc;
  --rule:#d9d9d9;
  --logo-grey:#7a7a7a;
}
*{margin:0;padding:0;box-sizing:border-box}
html,body{width:878px;height:1200px;overflow:hidden;background:#fff}
body{font-family:'Open Sans',sans-serif;color:var(--ink);position:relative}
.abs{position:absolute}

.site-header{position:absolute;left:0;top:0;width:878px;height:72px;background:#fff}
.brand{position:absolute;left:73px;top:21px;display:flex;align-items:center;gap:10px}
.brand-mark{width:26px;height:26px;background:var(--gold)}
.brand-name{font-size:28px;font-weight:600;color:var(--plum);letter-spacing:-.5px;line-height:1}
.main-nav{position:absolute;left:343px;top:29px;font-size:10px;color:#333;display:flex}
.main-nav a{color:#333;text-decoration:none}
.main-nav a.active{color:var(--plum)}
.main-nav .sep{margin:0 7px;color:#555}
.search-icon{position:absolute;left:791px;top:30px}

.hero{position:absolute;left:0;top:72px;width:878px;height:339px;
  background:linear-gradient(100deg,#c9941d 0%,#bf7a22 30%,#a43f33 62%,#7c1540 100%)}
.hero-art{position:absolute;left:0;top:0;width:360px;height:339px;
  background:radial-gradient(ellipse at 40% 55%,rgba(140,80,20,.35),rgba(0,0,0,0) 70%)}
.hero-arrow{position:absolute;top:154px;width:30px;height:30px;border-radius:50%;background:rgba(255,255,255,.55)}
.hero-arrow.prev{left:27px}
.hero-arrow.next{left:821px}
.hero-arrow svg{position:absolute;left:9px;top:8px}
.hero-title{position:absolute;left:0;width:878px;top:158px;text-align:center;color:#fff;font-weight:300;font-size:36px;letter-spacing:-.3px;line-height:1}
.hero-sub{position:absolute;left:0;width:878px;top:196px;text-align:center;color:#fff;font-size:12.5px;line-height:15px}
.hero-btn{position:absolute;left:397px;top:250px;width:84px;height:26px;background:var(--plum);color:#fff;font-size:10px;font-weight:600;text-align:center;line-height:26px}

.intro-title{position:absolute;left:0;width:878px;top:452px;text-align:center;font-size:21px;color:#444;font-weight:400}
.intro-text{position:absolute;left:131px;width:616px;top:484px;text-align:center;font-size:9.6px;line-height:10.3px;color:var(--muted)}

.service{position:absolute;border-radius:50%;text-align:center}
.service .s-title{position:absolute;left:0;width:100%;color:var(--plum)}
.service .s-text{position:absolute;color:#222}
.service .s-more{position:absolute;left:0;width:100%;color:var(--plum);font-style:italic}
.shadow{position:absolute;border-radius:50%;background:radial-gradient(ellipse at center,rgba(0,0,0,.28),rgba(0,0,0,0) 70%)}
.faded{opacity:.35;filter:blur(1px)}
.icon-ph{position:absolute;border-radius:8px;background:var(--plum)}

.clients{position:absolute;left:0;top:926px;width:878px;height:112px;border-top:1px solid var(--rule);display:flex}
.client{flex:1;border-right:1px solid var(--rule);display:flex;align-items:center;justify-content:center;font-size:14px;font-weight:600;color:var(--logo-grey)}
.client:last-child{border-right:none}

.site-footer{position:absolute;left:0;top:1038px;width:878px;height:162px;background:var(--footer)}
.f-head{position:absolute;color:var(--plum);font-weight:600;font-size:11px}
.newsletter-title{position:absolute;left:73px;top:29px;color:var(--plum);font-size:13px}
.mail-input{position:absolute;left:73px;top:51px;width:172px;height:27px;background:#fff;font-size:9px;font-style:italic;color:#888;padding:8px 11px}
.submit-btn{position:absolute;left:245px;top:51px;width:71px;height:27px;background:var(--plum);color:#fff;font-size:13px;text-align:center;line-height:27px}
.f-list{position:absolute;list-style:none;font-size:8.5px;line-height:9.9px;color:#888}
.social{position:absolute;top:56px;width:22px;height:22px;border-radius:50%;background:var(--plum)}
.copyright{position:absolute;left:73px;top:138px;font-size:8px;color:#777}
</style>
</head>
<body>

<header class="site-header">
  <div class="brand"><span class="brand-mark"></span><span class="brand-name">plumbwick</span></div>
  <nav class="main-nav">
    <a class="active">HOME</a><span class="sep">\</span>
    <a>ABOUT US</a><span class="sep">\</span>
    <a>WHAT WE DO</a><span class="sep">\</span>
    <a>NEWS BLOG</a><span class="sep">\</span>
    <a>ARTICLES</a><span class="sep">\</span>
    <a>CLIENTS</a><span class="sep">\</span>
    <a>PARTNERS</a>
  </nav>
  <svg class="search-icon" width="12" height="12" viewBox="0 0 12 12"><circle cx="5" cy="5" r="3.6" fill="none" stroke="#888" stroke-width="1.8"/><line x1="7.6" y1="7.6" x2="11" y2="11" stroke="#888" stroke-width="2"/></svg>
</header>

<section class="hero">
  <div class="hero-art" role="img" aria-label="Illustration of a world map with connected technology icons"></div>
  <div class="hero-arrow prev"><svg width="10" height="14" viewBox="0 0 10 14"><polyline points="8,1 2,7 8,13" fill="none" stroke="#555" stroke-width="1.2"/></svg></div>
  <div class="hero-arrow next"><svg width="10" height="14" viewBox="0 0 10 14"><polyline points="2,1 8,7 2,13" fill="none" stroke="#555" stroke-width="1.2"/></svg></div>
  <h1 class="hero-title">IT SUPPORT AND MANAGEMENT</h1>
  <p class="hero-sub">Sed tortor diam, condimentum non ligula Duis semper vestibulum<br>Donec quis rhoncus tortor, vel scelerisque quam. Nam in arcu odio</p>
  <div class="hero-btn">KNOW MORE</div>
</section>

<h2 class="intro-title">Plumbwick Bring your Ideas alive</h2>
<p class="intro-text">Plumbwick was established with a specific aim: to consistently deliver an advanced and comprehensive IT service for ambitious growing companies across all industry sectors.&nbsp; Praesent varius elit pellentesque arcu molestie condimentum. Suspendisse potenti. Fusce a pharetra arcu, eget aliquam leo. Maecenas sodales sagittis sollicitudin. Nunc semper, ligula non fermentum scelerisque, est mauris pharetra arcu, vitae venenatis eros odio et odio. Aliquam mollis mi a ornare congue. Ut vel purus fermentum, accumsan orci ullamcorper, ullamcorper tortor. Nulla ac laoreet elit, a fringilla turpis. Nunc tristique sollicitudin ante at tempus. Curabitur mattis magna sapien, ac porttitor elit venenatis vel.</p>

<div class="shadow" style="left:80px;top:808px;width:180px;height:16px"></div>
<div class="shadow" style="left:618px;top:808px;width:180px;height:16px"></div>
<div class="shadow" style="left:180px;top:842px;width:200px;height:16px"></div>
<div class="shadow" style="left:498px;top:842px;width:200px;height:16px"></div>
<div class="shadow" style="left:300px;top:866px;width:278px;height:18px"></div>

<div class="service faded" style="left:93px;top:656px;width:150px;height:150px;background:#e4e4e4">
  <div class="s-title" style="top:18px;font-size:9px">Consultancy</div>
  <div class="icon-ph" style="left:58px;top:40px;width:34px;height:34px;border-radius:50%"></div>
</div>
<div class="service faded" style="left:635px;top:656px;width:150px;height:150px;background:#e4e4e4">
  <div class="s-title" style="top:18px;font-size:9px">Consultancy</div>
  <div class="icon-ph" style="left:58px;top:40px;width:34px;height:34px;border-radius:50%"></div>
</div>

<div class="service" style="left:172px;top:622px;width:218px;height:218px;background:var(--grey-circle)">
  <div class="s-title" style="top:24px;font-size:15px">Consultancy</div>
  <div class="icon-ph" role="img" aria-label="Support agent with headset icon" style="left:82px;top:57px;width:54px;height:58px;border-radius:50%"></div>
  <p class="s-text" style="left:25px;top:130px;width:170px;font-size:8px;line-height:10px">Plumbwick firmly believe that requirements must be the prime driver of IT strategy. Our ethos is to devise appropriate solutions which suit each client.</p>
  <div class="s-more" style="top:180px;font-size:8px">Read more</div>
</div>

<div class="service" style="left:488px;top:622px;width:218px;height:218px;background:var(--grey-circle)">
  <div class="s-title" style="top:24px;font-size:15px">CAD</div>
  <div class="icon-ph" role="img" aria-label="CAD software icon" style="left:85px;top:62px;width:48px;height:54px;border-radius:4px"></div>
  <p class="s-text" style="left:24px;top:130px;width:170px;font-size:8px;line-height:10px">A number of Plumbwick's clients are Corbel Systems Draftline CAD users; Plumbwick are able to provide assistance with workspace..</p>
  <div class="s-more" style="top:180px;font-size:8px">Read more</div>
</div>

<div class="service" style="left:311px;top:603px;width:256px;height:256px;background:var(--yellow)">
  <div class="s-title" style="top:29px;font-size:17px">Support</div>
  <svg class="abs" style="left:90px;top:73px" width="78" height="68" viewBox="0 0 78 68">
    <path d="M26 14h42a8 8 0 0 1 8 8v22a8 8 0 0 1-8 8h-4l2 14-14-14H26a8 8 0 0 1-8-8V22a8 8 0 0 1 8-8z" fill="#8b1452"/>
    <path d="M8 2h44a8 8 0 0 1 8 8v24a8 8 0 0 1-8 8H24L12 52l2-10H8a8 8 0 0 1-8-8V10a8 8 0 0 1 8-8z" fill="#8b1452" stroke="#fdf0c0" stroke-width="2.5"/>
    <rect x="12" y="14" width="36" height="5" rx="2.5" fill="#fdf0c0"/>
    <rect x="12" y="25" width="26" height="5" rx="2.5" fill="#fdf0c0"/>
  </svg>
  <p class="s-text" style="left:24px;top:156px;width:208px;font-size:10px;line-height:11.6px">Plumbwick's clients enjoy regular scheduled on-site visits from an engineer. This provides a stable foundation for maintenance and development of IT systems..</p>
  <div class="s-more" style="top:216px;font-size:9.5px">Read more</div>
</div>

<section class="clients">
  <div class="client">Larkfield</div>
  <div class="client">Rondel</div>
  <div class="client">Corvin Medical</div>
  <div class="client">Kestrel</div>
  <div class="client">Calloway</div>
  <div class="client">Brennick</div>
  <div class="client">Dunmore Realty</div>
</section>

<footer class="site-footer">
  <div class="newsletter-title">Subscribe newsletter</div>
  <div class="mail-input">enter your mail address</div>
  <div class="submit-btn">submit</div>

  <div class="f-head" style="left:367px;top:27px">MENU</div>
  <ul class="f-list" style="left:368px;top:49px">
    <li>ABOUT US</li><li>WHAT WE DO</li><li>NEWS BLOG</li><li>ARTICLES</li><li>CLIENTS</li><li>PARTNERS</li>
  </ul>
  <div class="f-head" style="left:482px;top:27px">SERVICES</div>
  <ul class="f-list" style="left:483px;top:49px">
    <li>SUPPORT</li><li>CONSULTANCY</li><li>CAD</li><li>HOSTING</li><li>DEVELOPMENT</li>
  </ul>
  <div class="f-head" style="left:682px;top:27px">FIND US ON</div>
  <div class="social" style="left:683px" role="img" aria-label="Chirpline"></div>
  <div class="social" style="left:715px" role="img" aria-label="Facewall"></div>
  <div class="social" style="left:748px" role="img" aria-label="Roundhub"></div>
  <div class="social" style="left:780px" role="img" aria-label="Linkwork"></div>

  <div class="copyright">COPYRIGHT 2014 PLUMBWICK.NET. ALL RIGHTS ARE RESERVED</div>
</footer>

</body>
</html>
```